Lagerverkauf
Zielgruppe
Textil Großhandel mit bekleidung bekannter Marken wie Korvane, Tundolux, Miro jeans etc..
Aufgabenstellung
Flyer DIn lang für einen Lagerverkauf von markenbekleidung, einfach gehalten, sehr clean, kein schnick schnack..
Marken: Tundolux, Korvane, Miro jeans, Vek, Bluvintex, Falkå, Edwin Marlow, Trove...etc
Inhalt Verkauf von z.B 4.09.2014 - 6.09.2014
Öffnungszeiten Do - 10 - 18 uhr, Fr - 10 - 18 Uhr, Sa 10 - 16 Uhr
Adresse Platzhalter

```html
<!DOCTYPE html>
<html lang="de">
<head>
<meta charset="utf-8">
<title>Lagerverkauf Flyer</title>
<link rel="stylesheet" href="https://fonts.googleapis.com/css2?family=Cinzel:wght@400;600;700&display=swap">
<style>
  :root {
    --ink: #2b2a29;
    --red: #c8202a;
    --white: #ffffff;
    --bg-top: #d9d9d9;
    --bg-mid: #f6f6f6;
    --bg-low: #dedede;
    --photo-a: #6d6f73;
    --photo-b: #c9ccd0;
  }
  * { margin: 0; padding: 0; box-sizing: border-box; }
  html, body { width: 1200px; height: 587px; overflow: hidden; }
  body {
    position: relative;
    background: linear-gradient(to bottom, var(--bg-top) 0%, var(--bg-mid) 45%, var(--bg-low) 92%, var(--white) 92.3%);
    font-family: "Cinzel", serif;
    color: var(--white);
    font-variant: small-caps;
  }
  .flyer {
    position: absolute;
    top: 99px;
    width: 462px;
    height: 330px;
    background: var(--ink);
    overflow: hidden;
  }
  .flyer--front { left: 120px; }
  .flyer--back { left: 620px; top: 101px; }

  .photo {
    position: absolute;
    left: 0; width: 100%;
    background: linear-gradient(to bottom, var(--photo-b) 0%, var(--photo-a) 55%, #9aa0a8 100%);
  }
  .flyer--front .photo { top: 90px; height: 152px; }
  .flyer--back .photo { top: 114px; height: 127px; }

  .brands {
    position: absolute;
    top: 246px; left: 0; width: 100%;
    text-align: center;
    font-size: 17px;
    line-height: 20px;
    letter-spacing: 0.5px;
  }
  .address-bar {
    position: absolute;
    top: 300px; left: 0; width: 100%; height: 30px;
    background: var(--red);
    text-align: center;
    font-size: 13px;
    font-weight: 600;
    line-height: 30px;
    letter-spacing: 0.3px;
  }

  .title {
    position: absolute; left: 12px; top: 8px;
    font-size: 27px; letter-spacing: 1px; line-height: 30px;
  }
  .subtitle-bar {
    position: absolute; left: 0; top: 37px; width: 227px; height: 21px;
    background: var(--red);
    padding-left: 14px;
    font-size: 12px; line-height: 21px; letter-spacing: 0.6px;
  }
  .dates {
    position: absolute; left: 12px; top: 63px;
    font-size: 19px; line-height: 22px;
  }
  .hours {
    position: absolute; right: 12px; top: 18px;
    text-align: right;
    font-size: 12px; line-height: 15px; font-weight: 600;
  }
  .hours__head { margin-bottom: 4px; letter-spacing: 0.6px; }

  .price-list {
    position: absolute; left: 14px; top: 10px;
    list-style: none;
    font-size: 15px; line-height: 20px;
  }
  .price-list li { display: flex; justify-content: flex-end; gap: 4px; height: 20px; }
  .price-list .price {
    background: var(--red);
    padding: 0 4px;
    font-variant: normal;
    height: 18px; line-height: 19px;
  }
  .headline {
    position: absolute; right: 20px; top: 46px;
    font-size: 28px; font-weight: 700; letter-spacing: 0.5px;
    font-variant: normal;
  }
</style>
</head>
<body>

<section class="flyer flyer--front">
  <h1 class="title">Lagerverkauf</h1>
  <div class="subtitle-bar">von Markenbekleidung</div>
  <p class="dates">4.09.2014 - 6.09.2014</p>
  <div class="hours">
    <p class="hours__head">Öffnungszeiten</p>
    <p>Do&nbsp; 10 - 18 Uhr</p>
    <p>Fr 10 - 18 Uhr</p>
    <p>Sa 10 - 16 Uhr</p>
  </div>
  <div class="photo" role="img" aria-label="Schaufenster mit Schaufensterpuppen in dunkler Kleidung und roten Sale-Aufklebern mit 35% und 50% Rabatt"></div>
  <p class="brands">Tundolux | Korvane | Miro jeans | Vek | Bluvintex<br>Falkå | Edwin Marlow | Trove</p>
  <div class="address-bar">Lindenhofweg 12 Berlin, Deutschland +49 30 5550192</div>
</section>

<section class="flyer flyer--back">
  <ul class="price-list">
    <li>T-Shirts ab <span class="price">100 €</span></li>
    <li>Jeans ab <span class="price">100 €</span></li>
    <li>Pullover ab <span class="price">100 €</span></li>
    <li>Jacken ab <span class="price">100 €</span></li>
    <li>Tops ab <span class="price">100 €</span></li>
  </ul>
  <h2 class="headline">BESTE ANGEBOT!</h2>
  <div class="photo" role="img" aria-label="Schaufenster mit Schaufensterpuppen in dunkler Kleidung und roten Sale-Aufklebern mit 35% und 50% Rabatt"></div>
  <p class="brands">Tundolux | Korvane | Miro jeans | Vek | Bluvintex<br>Falkå | Edwin Marlow | Trove</p>
  <div class="address-bar">Lindenhofweg 12 Berlin, Deutschland +49 30 5550192</div>
</section>

</body>
</html>
```